Website redesign www.marigoldlawpc.com law firm site

Need to redesign the website that I currently have to look more modern and professional. Would also like to be able to make updates and post without having a huge hassle. See current www.marigoldlawpc.com. I just think that it looks very immature and it's very templated there's no ability for me to make posts or Add links or anything like that

Target Market(s)

California people looking for a powerhouse attorney in

Industry/Entity Type

Legal

Number of Pages Required

3 page

Font styles to use
Serif
Sans Serif

Colors
ec1f27
000000
ffffff

Requirements
Must have
• Must be mobile friendly. Must look professional and have ability to post links to other websites. Must have ability to post blogs or articles. Would like to be able to read my FeeTrove account and also have the ability to upload forms for people to download
Nice to have
• Simple design easy to use and not cluttered with too much text

```html
<!DOCTYPE html>
<html lang="en">
<head>
<meta charset="utf-8">
<title>Marigold Law P.C.</title>
<link href="https://fonts.googleapis.com/css2?family=Cinzel:wght@400;700&family=Lato:wght@400;700&display=swap" rel="stylesheet">
<style>
:root{
  --red:#ec1f27;
  --black:#000;
  --white:#fff;
  --ink:#222;
  --grey:#5e5e5e;
  --badge:#b5b5b5;
  --footer:#2b2b2b;
}
*{margin:0;padding:0;box-sizing:border-box}
html,body{width:1200px;height:2821px;overflow:hidden;background:var(--white);font-family:'Lato',sans-serif;color:var(--ink)}
.wrap{width:1064px;margin:0 auto;position:relative}
.serif{font-family:'Cinzel',serif}

.site-header{height:107px;border-top:4px solid var(--black)}
.site-header .wrap{display:flex;justify-content:space-between;align-items:center;height:103px}
.brand{display:flex;align-items:center;gap:12px;font-family:'Lato',sans-serif;font-weight:700;font-size:30px;color:var(--black)}
.brand-mark{width:22px;height:22px;background:var(--red)}
.contact-top{font-size:15px;line-height:34px}
.contact-top div{display:flex;align-items:center;gap:10px}
.dot{width:20px;height:20px;border-radius:50%;background:var(--black);display:inline-flex;align-items:center;justify-content:center}

.main-nav{background:var(--black);height:44px}
.main-nav ul{list-style:none;display:flex;width:1064px;margin:0 auto;height:44px}
.main-nav li{flex:1;color:var(--white);font-size:15px;font-weight:700;display:flex;align-items:center;justify-content:center;border-right:1px solid #333}
.main-nav li.active{background:var(--red);flex:0 0 140px}

.hero{height:426px;position:relative;background:linear-gradient(90deg,#3a2418 0%,#6b4a35 45%,#8c6a50 70%,#4a3324 100%)}
.hero-art{position:absolute;right:120px;top:0;width:420px;height:426px;background:radial-gradient(ellipse at center,#b89a80 0%,rgba(110,80,60,0) 70%)}
.hero-copy{position:absolute;left:68px;top:112px;color:var(--white);font-family:'Cinzel',serif;font-size:27px;line-height:38px;letter-spacing:.5px}
.btn-outline{position:absolute;left:68px;top:288px;border:2px solid var(--white);color:var(--white);font-family:'Cinzel',serif;font-size:24px;padding:12px 24px}
.arrow{position:absolute;top:176px}

.welcome{height:467px}
.welcome .wrap{display:flex;justify-content:space-between;padding-top:65px}
.welcome-text{width:680px}
.welcome h1{font-family:'Cinzel',serif;font-weight:400;font-size:35px;padding-bottom:10px;border-bottom:1px solid #999;margin-bottom:14px}
.welcome h1 span{color:var(--red)}
.welcome p{font-size:15px;line-height:25px;margin-bottom:12px}
.pill{display:inline-flex;align-items:center;background:var(--grey);color:var(--white);font-size:11px;font-weight:700;height:36px;border-radius:18px;padding-left:12px;gap:12px}
.pill i{width:40px;height:40px;border-radius:50%;background:var(--black);display:flex;align-items:center;justify-content:center;border:2px solid var(--white)}
.inquiry{width:329px;height:337px;background:var(--grey);margin-top:-24px;padding:26px 18px}
.inquiry h2{font-family:'Cinzel',serif;font-weight:400;color:var(--white);font-size:31px;text-align:center;margin-bottom:20px}
.field{background:var(--white);height:40px;margin-bottom:9px;font-size:13px;color:#555;padding:12px 10px}
.field.tall{height:76px}

.practice{background:var(--black);height:401px;color:var(--white);text-align:center;position:relative}
.practice h2{font-family:'Cinzel',serif;font-weight:400;font-size:34px;padding-top:52px}
.rule{width:300px;height:1px;background:#888;margin:14px auto 0;position:relative}
.rule:after{content:"";position:absolute;left:147px;top:-3px;width:7px;height:7px;border-radius:50%;background:var(--white)}
.areas{display:flex;justify-content:space-between;width:945px;margin:40px auto 0}
.area{width:140px;font-size:18px;font-weight:700;line-height:24px}
.area .ring{width:136px;height:136px;border-radius:50%;border:2px solid var(--white);margin:0 auto 12px;display:flex;align-items:center;justify-content:center}
.area.on .ring{background:var(--white)}

.attorney{height:372px;background:linear-gradient(90deg,#e7e7e7,#f7f7f7 60%,#dcdcdc)}
.attorney .wrap{display:flex;gap:56px;padding-top:48px}
.photo{width:247px;height:247px;background:var(--black);padding:10px;flex:none}
.photo div{width:100%;height:100%;border:2px solid var(--white);background:linear-gradient(135deg,#6a4a38,#b88e72 55%,#3b2a20)}
.att-text .label{font-size:20px;margin-top:20px}
.att-text h2{font-family:'Cinzel',serif;font-weight:400;font-size:32px;color:var(--red);border-bottom:1px solid #999;padding-bottom:6px;margin-bottom:12px}
.att-text h2 span{color:var(--black);font-size:20px}
.att-text p{font-size:13.5px;line-height:22px;width:760px}
.redpill{display:inline-flex;align-items:center;background:var(--red);color:var(--white);font-size:12px;line-height:14px;height:36px;padding-left:10px;gap:10px;margin-top:12px;border-radius:0 18px 18px 0}
.redpill i{width:40px;height:40px;border-radius:50%;background:var(--black);display:flex;align-items:center;justify-content:center;border:2px solid var(--white)}

.news{height:497px;background:linear-gradient(90deg,#151110,#2a211b 50%,#171312);color:var(--white)}
.news .wrap{display:flex;justify-content:space-between;padding-top:52px}
.col{width:446px}
.col-head{display:flex;justify-content:space-between;align-items:center;border-bottom:1px solid #666;padding-bottom:10px;margin-bottom:22px}
.col-head h2{font-family:'Cinzel',serif;font-weight:400;font-size:30px}
.ctrl{display:flex;gap:4px}
.ctrl span{width:16px;height:16px;border:2px solid var(--white);border-radius:50%}
.post{display:flex;gap:12px;margin-bottom:28px}
.thumb{width:88px;height:58px;background:linear-gradient(135deg,#c9c2b8,#6d655c);border:2px solid #ddd;flex:none}
.post h3{font-size:13.5px;margin-bottom:6px}
.post p{font-size:14px;line-height:19px;color:#ddd}
.post a{color:var(--red);font-size:11px;text-decoration:underline}
.quote{display:flex;gap:18px;margin-bottom:22px}
.avatar{width:118px;height:118px;border-radius:50%;border:4px solid var(--white);background:linear-gradient(135deg,#8a6b55,#d6b89c);flex:none}
.quote p{font-size:13px;line-height:20px;color:#ddd}
.quote cite{display:block;font-family:'Cinzel',serif;font-style:normal;color:var(--red);font-size:13px;margin-top:6px;border-bottom:1px solid #777;padding-bottom:6px}

.ratings{height:192px;display:flex;align-items:center;justify-content:center;gap:50px}
.ratings h2{font-family:'Cinzel',serif;font-weight:400;font-size:30px;letter-spacing:1px}
.badge-round{width:96px;height:96px;border-radius:50%;background:var(--badge)}
.badge-bar{width:240px;height:40px;background:var(--badge)}

.site-footer{background:var(--footer);height:265px;color:var(--white)}
.site-footer .wrap{display:flex;padding-top:38px;gap:40px}
.site-footer h4{font-family:'Cinzel',serif;font-weight:400;font-size:19px;border-bottom:1px solid #666;padding-bottom:8px;margin-bottom:14px}
.links li{list-style:none;font-size:13px;line-height:21px}
.links li:before{content:"› "}
.nl p{font-size:13px;line-height:20px;margin-bottom:20px}
.nl .input{border:1px solid #ccc;height:34px;font-size:13px;padding:9px 10px;margin-bottom:12px}
.nl .sub{display:inline-block;background:var(--white);color:var(--black);font-size:12px;font-weight:700;padding:7px 12px}
.map{width:260px;height:132px;background:linear-gradient(135deg,#d8e0d2,#f0eee6 50%,#cfd8e6)}
.cd{font-size:13px;line-height:22px}
.cd div{display:flex;gap:12px;margin-bottom:6px;align-items:flex-start}
.cd svg{margin-top:5px;flex:none}

.bottom{background:var(--black);height:50px;color:var(--white);font-size:12px}
.bottom .wrap{display:flex;justify-content:space-between;align-items:center;height:50px}
.social{display:flex;align-items:center;gap:10px}
.social span{width:30px;height:30px;border-radius:50%;background:#2d6cc0}
</style>
</head>
<body>

<header class="site-header">
  <div class="wrap">
    <div class="brand"><span class="brand-mark"></span>Marigold Law P.C.</div>
    <div class="contact-top">
      <div><span class="dot"><svg width="10" height="10" viewBox="0 0 10 10"><path d="M2 1l2 2-1 1c.5 1.2 1.3 2 2.5 2.5l1-1 2 2-1.5 1.5C4 8.5 1.5 6 .5 2.5z" fill="#fff"/></svg></span>(555) 014-2290</div>
      <div><span class="dot"><svg width="11" height="8" viewBox="0 0 11 8"><rect x=".5" y=".5" width="10" height="7" fill="none" stroke="#fff"/><path d="M.5 .5l5 4 5-4" fill="none" stroke="#fff"/></svg></span>renee@marigoldlawgroup.com</div>
    </div>
  </div>
</header>

<nav class="main-nav">
  <ul>
    <li class="active">Home</li><li>Attorney Profile</li><li>Practice Area ▾</li><li>Client Reviews</li><li>Links</li><li>Contact us</li>
  </ul>
</nav>

<section class="hero">
  <div class="hero-art" role="img" aria-label="Brass scales of justice in a courtroom"></div>
  <svg class="arrow" style="left:24px" width="22" height="96" viewBox="0 0 22 96"><path d="M20 2L2 48l18 46" fill="none" stroke="#fff" stroke-width="2"/></svg>
  <svg class="arrow" style="right:24px" width="22" height="96" viewBox="0 0 22 96"><path d="M2 2l18 46L2 94" fill="none" stroke="#fff" stroke-width="2"/></svg>
  <p class="hero-copy">A boutique law firm opportunity<br>for clients who want to enjoy all<br>the advantages of Renee's broad<br>legal experience and education.</p>
  <div class="btn-outline">Call Us Today</div>
</section>

<section class="welcome">
  <div class="wrap">
    <div class="welcome-text">
      <h1>Welcome to <span>Marigold Law P.C</span></h1>
      <p>At Marigold Law, P.C., we offer the following clients services to help you manage all areas of your life that may ever need legal attention</p>
      <p>Marigold Law P.C. is owned by Renee L. Marigold, a dedicated and caring professional who uses her broad range of skills as a California lawyer to bring consumers and business owners exceptionally strong legal representation that achieves best results. She works with people from across the northern region of California, from the Northern border to the Central Valley region. They bring her legal concerns and problems that occur in many areas of law, including Real Estate, Family law, Business Law, Bankruptcy, Criminal Law and Civil Litigation</p>
      <span class="pill">READ MORE <i><svg width="10" height="12" viewBox="0 0 10 12"><path d="M2 1l6 5-6 5" fill="none" stroke="#fff" stroke-width="2"/></svg></i></span>
    </div>
    <form class="inquiry">
      <h2>Quick Inquiry</h2>
      <div class="field">Name</div>
      <div class="field">Email</div>
      <div class="field tall">Message</div>
      <span class="pill" style="background:#9a9a9a;margin-top:8px">SUBMIT <i><svg width="10" height="12" viewBox="0 0 10 12"><path d="M2 1l6 5-6 5" fill="none" stroke="#fff" stroke-width="2"/></svg></i></span>
    </form>
  </div>
</section>

<section class="practice">
  <h2>Our Practice Areas</h2>
  <div class="rule"></div>
  <svg class="arrow" style="left:24px;top:205px" width="22" height="66" viewBox="0 0 22 66"><path d="M20 2L2 33l18 31" fill="none" stroke="#fff" stroke-width="2"/></svg>
  <svg class="arrow" style="right:24px;top:205px" width="22" height="66" viewBox="0 0 22 66"><path d="M2 2l18 31L2 64" fill="none" stroke="#fff" stroke-width="2"/></svg>
  <div class="areas">
    <div class="area on"><div class="ring"><svg width="66" height="54" viewBox="0 0 66 54"><rect x="3" y="12" width="60" height="38" rx="3" fill="none" stroke="#000" stroke-width="5"/><path d="M23 12V5h20v7M3 28h60" fill="none" stroke="#000" stroke-width="5"/></svg></div>Business<br>Law</div>
    <div class="area"><div class="ring"><svg width="64" height="60" viewBox="0 0 64 60"><path d="M4 30L32 6l28 24M12 24v32h40V24" fill="none" stroke="#fff" stroke-width="5"/><rect x="24" y="34" width="16" height="22" fill="#fff"/></svg></div>Real Estate<br>Law</div>
    <div class="area"><div class="ring"><svg width="64" height="64" viewBox="0 0 64 64"><circle cx="32" cy="32" r="28" fill="#fff"/><text x="32" y="45" text-anchor="middle" font-family="Lato,sans-serif" font-weight="700" font-size="38" fill="#000">$</text></svg></div>Bankruptcy</div>
    <div class="area"><div class="ring"><svg width="64" height="60" viewBox="0 0 64 60"><path d="M4 26L32 4l28 22" fill="none" stroke="#fff" stroke-width="5"/><circle cx="20" cy="28" r="6" fill="#fff"/><circle cx="44" cy="28" r="6" fill="#fff"/><circle cx="32" cy="38" r="4" fill="#fff"/><path d="M12 58V38h16v20zM36 58V38h16v20zM28 58V46h8v12z" fill="#fff"/></svg></div>Family<br>Law</div>
    <div class="area"><div class="ring"><svg width="66" height="50" viewBox="0 0 66 50"><circle cx="18" cy="30" r="13" fill="none" stroke="#fff" stroke-width="6"/><circle cx="48" cy="30" r="13" fill="none" stroke="#fff" stroke-width="6"/><path d="M24 10h18" stroke="#fff" stroke-width="6"/></svg></div>Criminal<br>Law</div>
  </div>
</section>

<section class="attorney">
  <div class="wrap">
    <div class="photo"><div role="img" aria-label="Portrait photo of attorney Renee L. Marigold"></div></div>
    <div class="att-text">
      <div class="label">Attorney Profile</div>
      <h2>Renee L. Marigold, Esq. <span>Attorney at Marigold Law P.C</span></h2>
      <p>Renee L. Marigold, Esq., is an Attorney who created a small boutique firm where she has the flexibility to build long-term, lasting relationships with clients. Renee provides all of her clients' legal needs through consultation, direct representation and/or qualified referrals. She recognizes the importance of client referrals, and works hard for her clients in every situation. Client referrals are the best way to grow a business, and Renee intends to have a superb reputation for being an excellent attorney and friend to her client base.</p>
      <span class="redpill">Call Us for<br>Free Consultation <i><svg width="10" height="12" viewBox="0 0 10 12"><path d="M2 1l6 5-6 5" fill="none" stroke="#fff" stroke-width="2"/></svg></i></span>
    </div>
  </div>
</section>

<section class="news">
  <div class="wrap">
    <div class="col">
      <div class="col-head"><h2>Blog Posts</h2><div class="ctrl"><span></span><span></span></div></div>
      <article class="post"><div class="thumb" role="img" aria-label="Blog post photo"></div><div><h3>Duis autem vel eum iriure dolor in hendrerit molestie</h3><p>Lorem ipsum dolor sit amet, consectetuer adipi diam nonummy nibh euismod tincidunt ut laoreet</p><a>Read More »</a></div></article>
      <article class="post"><div class="thumb" role="img" aria-label="Blog post photo"></div><div><h3>Duis autem vel eum iriure dolor in hendrerit molestie</h3><p>Lorem ipsum dolor sit amet, consectetuer adipi diam nonummy nibh euismod tincidunt ut laoreet</p><a>Read More »</a></div></article>
      <article class="post"><div class="thumb" role="img" aria-label="Blog post photo"></div><div><h3>Duis autem vel eum iriure dolor in hendrerit molestie</h3><p>Lorem ipsum dolor sit amet, consectetuer adipi diam nonummy nibh euismod tincidunt ut laoreet</p><a>Read More »</a></div></article>
    </div>
    <div class="col">
      <div class="col-head"><h2>Client Testimonials</h2><div class="ctrl"><span></span><span></span></div></div>
      <div class="quote"><div class="avatar" role="img" aria-label="Client portrait"></div><div><p>“ Marigold Law is our go-to source for professional and sound legal advice. Marigold Law has become a vital component to the success of our business as well as the businesses of the clients we have referred to Marigold Law. ”</p><cite>Harbor Ridge Accounting Group</cite></div></div>
      <div class="quote"><div class="avatar" role="img" aria-label="Client portrait"></div><div><p>“ Marigold Law has met and exceeded our expectations in assisting our company with our real estate legal needs. In an area of law where the rules our ever changing, we simply could not navigate our company effectively without their help. ”</p><cite>Linden Commercial</cite></div></div>
    </div>
  </div>
</section>

<section class="ratings">
  <h2>Ratings and Reviews:</h2>
  <div class="badge-round" role="img" aria-label="Attorney rating badge"></div>
  <div class="badge-round" role="img" aria-label="Bar association seal"></div>
  <div class="badge-bar" role="img" aria-label="Lawyer directory listing"></div>
</section>

<footer class="site-footer">
  <div class="wrap">
    <div style="width:180px">
      <h4>Quick Links</h4>
      <ul class="links"><li>Home</li><li>Attorney Profile</li><li>Practice Area</li><li>Client Reviews</li><li>Links</li><li>Contact us</li></ul>
    </div>
    <div class="nl" style="width:240px">
      <h4>Newsletter Sign Up</h4>
      <p>Get latest update by entering your email address.</p>
      <div class="input">Email Address</div>
      <span class="sub">SUBSCRIBE</span>
    </div>
    <div style="width:544px;border-left:1px solid #555;padding-left:40px">
      <h4>Contact Details</h4>
      <div style="display:flex;gap:30px">
        <div class="map" role="img" aria-label="Office location map"></div>
        <div class="cd">
          <div><svg width="10" height="14" viewBox="0 0 10 14"><path d="M5 0a5 5 0 0 0-5 5c0 4 5 9 5 9s5-5 5-9a5 5 0 0 0-5-5z" fill="#fff"/><circle cx="5" cy="5" r="2" fill="#2b2b2b"/></svg><span><b>Marigold Law, P.C. Office</b><br>48 Orchard Avenue, Suite 210<br>Redding, CA 96001</span></div>
          <div><svg width="12" height="12" viewBox="0 0 10 10"><path d="M2 1l2 2-1 1c.5 1.2 1.3 2 2.5 2.5l1-1 2 2-1.5 1.5C4 8.5 1.5 6 .5 2.5z" fill="#fff"/></svg><span>(555) 014-2290</span></div>
          <div><svg width="12" height="12" viewBox="0 0 12 12"><rect x="1" y="4" width="10" height="7" fill="#fff"/><rect x="3" y="1" width="6" height="3" fill="#fff"/></svg><span>(555) 019-4471</span></div>
          <div><svg width="12" height="9" viewBox="0 0 11 8"><rect x=".5" y=".5" width="10" height="7" fill="none" stroke="#fff"/><path d="M.5 .5l5 4 5-4" fill="none" stroke="#fff"/></svg><span>renee@marigoldlawgroup.com</span></div>
        </div>
      </div>
    </div>
  </div>
</footer>

<div class="bottom">
  <div class="wrap">
    <span>Copyright © 2016 <b>Marigold Law P.C.</b> All Rights Reserved.</span>
    <span class="social"><b>Follow Us:</b><span></span><span></span><span></span></span>
    <span><b>Pay Your Invoice:</b> <span class="serif" style="font-size:16px">FeeTrove</span></span>
  </div>
</div>

</body>
</html>
```